Creation of an elegant and modern turnkey Shopify website

Hello,

We are a new company specializing in the sale of above-ground pools. We want to create a turnkey website, ideally using Shopify. For now, we need a "showcase" site, not an e-commerce platform, with four tabs:

Home Page (an overall presentation of the company)
Our Products (an overview of all the above-ground pools we sell)
Our Projects (a page inspired by Instagram to showcase photos of our future projects)
Contact (a page with all our contact information and a contact form)

We are looking to create a highly visual, elegant, and modern website with vibrant splashes of color. We will provide the text, photos (along with instructions on where to place them on each page), and all other necessary information as attachments.

Thank you in advance for your proposals!

The Brisa Lagoon Team

Target Market(s)

Targeted at Swiss customers (a translator will need to be installed for different languages)

Industry/Entity Type

Sale of customised above-ground pools

Coding

Coded - Design and coding required

Font styles to use
Sans Serif

Colors
0094D4
00A9DD
6FCCEA
C7EBF8
E9F6FB
00AB8E
00BBA5
67D7C9
C6EFE9
E9F9F6

Requirements
Must have
• A stunning, elegant and modern look
Nice to have
• Inspiration from the colors of our logo throughout the site, but in an elegant way
Should not have
• An overly classic look for swimming pool sites

```html
<!DOCTYPE html>
<html lang="en">
<head>
<meta charset="utf-8">
<title>Brisa Lagoon – Above-Ground Pools</title>
<link href="https://fonts.googleapis.com/css2?family=Lato:wght@400;700&family=Poppins:ital,wght@0,400;0,500;0,600;1,700&display=swap" rel="stylesheet">
<style>
:root{
  --teal:#00AB8E;
  --teal-2:#00BBA5;
  --teal-soft:#67D7C9;
  --blue:#0094D4;
  --blue-2:#00A9DD;
  --blue-soft:#6FCCEA;
  --ink:#1f1f1f;
  --muted:#555;
  --footer:#161616;
  --white:#fff;
}
*{margin:0;padding:0;box-sizing:border-box}
html,body{width:1200px;height:4552px;overflow:hidden}
body{font-family:"Lato",sans-serif;color:var(--ink);background:var(--white);position:relative}
.abs{position:absolute}
h2,h3,h4{font-family:"Poppins",sans-serif;font-weight:500}

/* top bar */
.topbar{top:0;left:0;width:1200px;height:60px;background:var(--teal);color:var(--white);font-size:15px}
.topbar .item{position:absolute;top:21px;display:flex;align-items:center;gap:10px}
/* nav */
.nav{top:60px;left:0;width:1200px;height:88px;background:var(--white)}
.nav a{position:absolute;top:34px;font-size:15px;color:#333;text-decoration:none}
.nav a.active{color:var(--teal)}
.brand{position:absolute;top:24px;left:520px;width:160px;text-align:center;font-family:"Lato",sans-serif;font-size:24px;color:var(--teal);line-height:1.05}
.nav .icons{position:absolute;top:32px;left:958px;display:flex;gap:28px}

/* hero */
.hero{top:148px;left:0;width:1200px;height:626px;background:linear-gradient(180deg,#2f4a2a 0%,#3d6340 30%,#3aa6c9 62%,#1f86b4 100%)}
.hero h1{position:absolute;left:110px;top:186px;font-family:"Poppins",sans-serif;font-weight:500;color:var(--white);font-size:30px;line-height:1.45;letter-spacing:.5px}
.hero h1 span{font-size:38px}
.hero p{position:absolute;left:110px;top:302px;width:520px;color:var(--white);font-size:15px;line-height:1.9}
.btn{display:inline-block;font-family:"Poppins",sans-serif;font-weight:600;font-size:15px;text-align:center;text-decoration:none}
.hero .btn{position:absolute;left:110px;top:393px;width:169px;height:40px;line-height:40px;background:var(--teal);color:var(--white)}
.circle-btn{position:absolute;width:34px;height:34px;border-radius:50%;background:var(--white);display:flex;align-items:center;justify-content:center}

/* section titles */
.title{font-family:"Poppins",sans-serif;font-weight:500;color:var(--teal);letter-spacing:.5px}

/* products */
.products-title{top:832px;left:0;width:1200px;text-align:center;font-size:30px}
.card{top:915px;width:260px;height:349px;border:1px solid #cfcfcf;padding:18px}
.card .photo{width:222px;height:178px}
.card h3{font-size:15px;font-weight:600;margin-top:20px;line-height:1.4;color:#222}
.card p{font-size:12px;color:#444;line-height:1.8;margin-top:10px}
.card .price{position:absolute;left:18px;bottom:22px;display:flex;align-items:baseline;gap:20px}
.card .old{font-size:11px;color:#999;text-decoration:line-through}
.card .new{font-family:"Poppins",sans-serif;font-size:16px;font-weight:500}

/* why band */
.why{top:1334px;left:0;width:1200px;height:455px;background:linear-gradient(180deg,#1aaf94,#16a98f)}
.why h2{position:absolute;top:68px;width:1200px;text-align:center;color:var(--white);font-size:30px}
.feature{position:absolute;top:150px;width:216px;text-align:center;color:var(--white)}
.feature .icon{width:112px;height:112px;border-radius:50%;border:4px solid var(--white);margin:0 auto}
.feature h3{font-size:18px;margin-top:14px}
.feature p{font-size:12.5px;line-height:2.2;margin-top:8px;color:#e9f9f6}

/* split sections */
.photo-block{position:absolute}
.copy{position:absolute}
.copy h2{font-size:30px;line-height:1.45}
.copy h4{font-family:"Lato",sans-serif;font-weight:700;font-size:19px;margin-top:26px;line-height:1.4}
.copy p{font-size:14px;line-height:2;color:#333;margin-top:28px}

/* contact band */
.contact-band{top:2320px;left:0;width:1200px;height:421px;background:linear-gradient(100deg,#2f7b8c 0%,#3d93a2 45%,#2a8aa6 100%)}
.contact-band h2{position:absolute;left:110px;top:82px;color:var(--white);font-size:30px}
.contact-band p{position:absolute;left:110px;top:144px;width:490px;color:var(--white);font-size:14.5px;line-height:2}
.contact-band .btn{position:absolute;left:110px;top:289px;width:170px;height:40px;line-height:40px;background:var(--white);color:var(--teal)}

/* cta band */
.cta{top:3319px;left:0;width:1200px;height:341px;background:var(--teal);text-align:center}
.cta h2{position:absolute;top:72px;width:1200px;font-style:italic;font-weight:700;color:var(--white);font-size:44px;line-height:1.4;letter-spacing:.5px}
.cta .btn{position:absolute;left:515px;top:219px;width:170px;height:42px;line-height:42px;background:var(--white);color:var(--teal)}

/* footer */
.footer{top:4174px;left:0;width:1200px;height:378px;background:var(--footer);color:var(--white)}
.fcol{position:absolute;top:62px}
.fcol h4{font-family:"Poppins",sans-serif;font-weight:600;color:var(--teal);font-size:24px;letter-spacing:1px}
.fcol p{font-size:14px;line-height:2;margin-top:26px}
.fcol ul{list-style:none;margin-top:24px}
.fcol li{font-size:15px;line-height:34px}
.fcol .row{display:flex;gap:16px;font-size:15px;line-height:28px}
.footer .rule{position:absolute;top:316px;left:110px;width:980px;height:1px;background:#bbb}
.footer .copyright{position:absolute;top:337px;width:1200px;text-align:center;font-size:14px}
</style>
</head>
<body>

<!-- top bar -->
<div class="abs topbar">
  <div class="item" style="left:110px">
    <svg width="16" height="16" viewBox="0 0 24 24" fill="#fff"><path d="M6.6 10.8a15 15 0 0 0 6.6 6.6l2.2-2.2c.3-.3.7-.4 1-.2 1.1.4 2.3.6 3.6.6.6 0 1 .4 1 1V20c0 .6-.4 1-1 1C10.6 21 3 13.4 3 4c0-.6.4-1 1-1h3.5c.6 0 1 .4 1 1 0 1.3.2 2.5.6 3.6.1.3 0 .7-.2 1z"/></svg>
    079 555 12 34
  </div>
  <div class="item" style="left:400px">
    <svg width="14" height="18" viewBox="0 0 24 30" fill="#fff"><path d="M12 0a10 10 0 0 0-10 10c0 7.5 10 20 10 20s10-12.5 10-20A10 10 0 0 0 12 0zm0 14a4 4 0 1 1 0-8 4 4 0 0 1 0 8z"/></svg>
    Marco Velani Rue des Tilleuls 22 1260 Nyon
  </div>
  <div class="item" style="left:1010px;top:20px">
    English
    <svg width="14" height="10" viewBox="0 0 14 10"><path d="M2 2l5 5 5-5" stroke="#fff" stroke-width="2.4" fill="none"/></svg>
  </div>
</div>

<!-- navigation -->
<nav class="abs nav">
  <a class="active" href="#" style="left:111px">Home</a>
  <a href="#" style="left:185px">Our Products</a>
  <a href="#" style="left:306px">Our Projects</a>
  <a href="#" style="left:424px">Contact Us</a>
  <div class="brand">Brisa<br>Lagoon</div>
  <div class="icons">
    <svg width="22" height="22" viewBox="0 0 24 24"><circle cx="10" cy="10" r="7" stroke="#00AB8E" stroke-width="3" fill="none"/><path d="M15 15l6 6" stroke="#00AB8E" stroke-width="3"/></svg>
    <svg width="20" height="22" viewBox="0 0 20 22" fill="#00AB8E"><circle cx="10" cy="6" r="5"/><path d="M1 21c0-5 4-8 9-8s9 3 9 8z"/></svg>
    <svg width="24" height="22" viewBox="0 0 24 22" fill="#00AB8E"><path d="M12 21 2.5 11.5A6 6 0 0 1 12 3.5a6 6 0 0 1 9.5 8z"/></svg>
  </div>
</nav>

<!-- hero -->
<section class="abs hero" role="img" aria-label="Child jumping into a round above-ground pool surrounded by garden hedges">
  <h1>WELCOME TO<br><span>BRISA LAGOON</span></h1>
  <p>Lorem ipsum dolor sit amet, consectetur adipiscing elit, sed do eiusmod tempor incididunt ut labore et dolore magna aliqua.</p>
  <a class="btn" href="#">GET STARTED</a>
  <div class="circle-btn" style="left:36px;top:296px"><svg width="16" height="16" viewBox="0 0 16 16"><path d="M10 2 4 8l6 6" stroke="#111" stroke-width="3" fill="none"/></svg></div>
  <div class="circle-btn" style="left:1094px;top:296px"><svg width="16" height="16" viewBox="0 0 16 16"><path d="M6 2l6 6-6 6" stroke="#111" stroke-width="3" fill="none"/></svg></div>
  <div class="circle-btn" style="left:582px;top:363px"><svg width="14" height="14" viewBox="0 0 14 14"><path d="M3 1l10 6-10 6z" fill="#00AB8E"/></svg></div>
</section>

<!-- products -->
<h2 class="abs title products-title">OUR PRODUCRS</h2>

<article class="abs card" style="left:65px">
  <div class="photo" role="img" aria-label="Family playing around an inflatable aluminium pool" style="background:linear-gradient(180deg,#5f8f3d,#8fc7c2 60%,#35a8d8)"></div>
  <h3>Aluminium Pools</h3>
  <p>Lorem ipsum dolor sit amet, consectetur adipiscing elit</p>
  <div class="price"><span class="old">$57.00</span><span class="new">$50.00</span></div>
</article>
<article class="abs card" style="left:338px">
  <div class="photo" role="img" aria-label="Couple relaxing in a bubbling mini pool spa" style="background:linear-gradient(180deg,#7fbfd6,#4fa6c8 50%,#d4ecf3)"></div>
  <h3>Mini Pool Spa</h3>
  <p>Lorem ipsum dolor sit amet, consectetur adipiscing elit</p>
  <div class="price"><span class="old">$57.00</span><span class="new">$50.00</span></div>
</article>
<article class="abs card" style="left:611px">
  <div class="photo" role="img" aria-label="Rectangular galvanized steel pool on a lawn" style="background:linear-gradient(180deg,#8fb0c8,#5e8a43 45%,#2ea3d2 70%,#555 100%)"></div>
  <h3>Galvanized Steel Pools With Composite Wood Coverings</h3>
  <p>Lorem ipsum dolor sit amet, consectetur</p>
  <div class="price"><span class="old">$57.00</span><span class="new">$50.00</span></div>
</article>
<article class="abs card" style="left:884px">
  <div class="photo" role="img" aria-label="Round above-ground pool with aluminium wall and ladder" style="background:linear-gradient(180deg,#4d5a3a,#c9c5b5 40%,#b8b3a2 80%,#8e8a7a)"></div>
  <h3>Above - Ground Pools With Aluminum AndWood</h3>
  <p>Lorem ipsum dolor sit amet, consectetur</p>
  <div class="price"><span class="old">$57.00</span><span class="new">$50.00</span></div>
</article>

<!-- why choose -->
<section class="abs why">
  <h2>WHY CHOOSE OUR ABOVE-GROUND POOLS?</h2>
  <div class="feature" style="left:40px">
    <div class="icon" role="img" aria-label="Top view of a pool with a swimmer" style="background:radial-gradient(circle,#d8eef1,#7cc4c4)"></div>
    <h3>Superior Quality</h3>
    <p>Each pool is constructed with high-quality materials, ensuring exceptional durability and strength.</p>
  </div>
  <div class="feature" style="left:274px">
    <div class="icon" role="img" aria-label="Pool with clear blue water" style="background:linear-gradient(180deg,#5a6e4a,#2fb3d3)"></div>
    <h3>Elegant Design</h3>
    <p>Our pools come in a variety of styles and finishes, seamlessly blending into any garden setting.</p>
  </div>
  <div class="feature" style="left:509px">
    <div class="icon" role="img" aria-label="Blue inflatable round pool" style="background:radial-gradient(circle,#3e86d8,#0d4fa6)"></div>
    <h3>Custom and Tailor</h3>
    <p>Create the pool of your dreams with our customization options, tailored to your specific tastes and needs.</p>
  </div>
  <div class="feature" style="left:726px">
    <div class="icon" role="img" aria-label="Square pool being filled on a terrace" style="background:linear-gradient(180deg,#7ea39a,#3fbdc6)"></div>
    <h3>Easy Installation</h3>
    <p>Enjoy your new oasis quickly with our simple and fast installation process.</p>
  </div>
  <div class="feature" style="left:944px">
    <div class="icon" role="img" aria-label="Pool float ring on the water" style="background:radial-gradient(circle,#e98aa0,#d7e9ee 70%)"></div>
    <h3>Constant Innovation</h3>
    <p>We incorporate the latest technologies to provide you with an optimal and safe swimming</p>
  </div>
</section>

<!-- guaranteed satisfaction -->
<div class="photo-block" role="img" aria-label="Pool with white fence and palm trees under a blue sky" style="left:110px;top:1875px;width:447px;height:385px;background:linear-gradient(180deg,#bfe0f5,#9fc3d9 30%,#4d7d3f 55%,#d8d8d8 72%,#27a7d6 88%)"></div>
<div class="copy" style="left:599px;top:1945px;width:480px">
  <h2 class="title">GUARANTEED SATISFACTION</h2>
  <h4 style="font-size:19px;margin-top:18px">10-Year Warranty!</h4>
  <p>Your satisfaction is our top priority. We are committed to providing you with exceptional service and the highest quality products. Join our community of satisfied customers who are already enjoying their custom above-ground pools.</p>
</div>

<!-- contact band -->
<section class="abs contact-band" role="img" aria-label="Man relaxing on an inflatable lounger in a pool with a drink">
  <h2>CONTACT US TODAY</h2>
  <p>Don't wait any longer to transform your garden into a wellness oasis. Contact us today to discover our range of customizable above-ground pools and get a tailored quote. Dive into a world of infinite possibilities with [Your Company Name].</p>
  <a class="btn" href="#">CONTACT NOW</a>
</section>

<!-- transform your garden -->
<div class="photo-block" role="img" aria-label="Wooden-clad round pool on a timber deck in a garden" style="left:110px;top:2828px;width:447px;height:385px;background:linear-gradient(180deg,#4b7a35,#6c9b4c 35%,#3aa6c9 48%,#b0683a 60%,#c7805a 100%)"></div>
<div class="copy" style="left:599px;top:2820px;width:490px">
  <h2 class="title">TRANSFORM YOUR GARDEN WITH OUR PREMIUM ABOVE-GROUND POOLS!</h2>
  <h4>Achieve your dreams with our custom, tailor-made above-ground pools.</h4>
  <p>Imagine an exceptional relaxation and leisure space right in your own backyard. With our unparalleled expertise and commitment to excellence, we create above-ground pools that exceed all expectations. Our exclusive, custom-designed models are crafted to combine style, durability, and innovation, offering a unique and refined experience.</p>
</div>

<!-- cta band -->
<section class="abs cta">
  <h2>WE BRING YOUR POOL<br>DREAMS TO LIFE!</h2>
  <a class="btn" href="#">CLICK HERE</a>
</section>

<!-- personalized services -->
<div class="copy" style="left:110px;top:3815px;width:470px">
  <h2 class="title">PERSONALIZED SERVICES</h2>
  <p style="margin-top:30px">We understand that every garden and client is unique. That's why we offer personalized services, from design to installation and after-sales support. Our team of experts is here to answer all your questions and guide you throughout your project.</p>
</div>
<div class="photo-block" role="img" aria-label="Inflatable blue pool on a tiled garden terrace" style="left:643px;top:3727px;width:446px;height:368px;background:linear-gradient(180deg,#5e8f44,#9fc77e 25%,#e8f3f7 40%,#4ab0e3 65%,#1f7fc8 100%)"></div>

<!-- footer -->
<footer class="abs footer">
  <div class="fcol" style="left:81px;width:290px">
    <h4>ABOUT US</h4>
    <p>Lorem ipsum dolor sit amet, consectetur adipiscing elit, sed do eiusmod tempor incididunt ut labore et dolore magna aliqua. Ut enim ad minim veniam, quis nostrud exercitation ullamco.</p>
  </div>
  <div class="fcol" style="left:406px">
    <h4>QUICK LINKS</h4>
    <ul><li>Terms of Service</li><li>Returns Policy</li><li>Our Products</li><li>Contact</li><li>Privacy Policy</li></ul>
  </div>
  <div class="fcol" style="left:657px">
    <h4>ABOUT INFO</h4>
    <ul><li>Home</li><li>About Us</li><li>Our Products</li><li>Our Projects</li><li>Contact Us</li></ul>
  </div>
  <div class="fcol" style="left:853px">
    <h4>CONTACT US</h4>
    <div class="row" style="margin-top:28px">
      <svg width="14" height="18" viewBox="0 0 24 30" fill="#00AB8E" style="margin-top:5px"><path d="M12 0a10 10 0 0 0-10 10c0 7.5 10 20 10 20s10-12.5 10-20A10 10 0 0 0 12 0zm0 14a4 4 0 1 1 0-8 4 4 0 0 1 0 8z"/></svg>
      <span>Marco Velani</span>
    </div>
    <div class="row"><span>Rue des Tilleuls 22 1260 Nyon</span></div>
    <div class="row" style="margin-top:12px">
      <svg width="16" height="16" viewBox="0 0 24 24" fill="#00AB8E" style="margin-top:6px"><path d="M6.6 10.8a15 15 0 0 0 6.6 6.6l2.2-2.2c.3-.3.7-.4 1-.2 1.1.4 2.3.6 3.6.6.6 0 1 .4 1 1V20c0 .6-.4 1-1 1C10.6 21 3 13.4 3 4c0-.6.4-1 1-1h3.5c.6 0 1 .4 1 1 0 1.3.2 2.5.6 3.6.1.3 0 .7-.2 1z"/></svg>
      <span>079 555 12 34</span>
    </div>
    <div class="row" style="margin-top:12px">
      <svg width="18" height="14" viewBox="0 0 18 14" style="margin-top:7px"><rect width="18" height="14" rx="2" fill="#00AB8E"/><path d="M1 2l8 6 8-6" stroke="#161616" stroke-width="1.6" fill="none"/></svg>
      <span>brisalagoon@example.com</span>
    </div>
  </div>
  <div class="rule"></div>
  <div class="copyright">Copyright © 2024 Brisa Lagoon. All rights reserved.</div>
</footer>

</body>
</html>
```